Need Help having my business card stand out

I am the owner of Birchway Canine Training and would like for my business cards to stand out. I have been trying to keep designing them myself but I can't get what I have in my head on the card. I will try my best to post templates that I like for inspirations. I want something unique but elegant. I don't want in to look cartoony or cheesy. It needs to pop in a pet shop but also in a coffee shop or gym.

Target Market(s)

Dog owners, Married ,No young kids Jr High school kids and up (maybe kids on the way) Executives, Stay at home moms/wives, Small business owners

Industry/Entity Type

Dog Training

Contact Information for Business Card

Lowell Spratt, 281-904-3376, info@birchwaycanine.example, www.birchwaycanine.example

Colors

Designer to choose colors to be used in the design.

Requirements
Must have
• my logo
Should not have
• Cursive lettering

```html
<!DOCTYPE html>
<html lang="en">
<head>
<meta charset="utf-8">
<title>Birchway Canine Training – Business Card</title>
<link href="https://fonts.googleapis.com/css2?family=Roboto+Condensed:wght@400&family=Crimson+Text:wght@400&display=swap" rel="stylesheet">
<style>
  :root {
    --page-bg: #e9e6e1;
    --card-black: #0d0d0d;
    --card-sheen: #262626;
    --band-black: #000000;
    --rule-grey: #8a8a8a;
    --badge-white: #ffffff;
    --badge-ring: #8c8c8c;
    --text-white: #f2f2f2;
    --text-soft: #cfcfcf;
    --ink: #111111;
  }
  * { margin: 0; padding: 0; box-sizing: border-box; }
  html, body { width: 1200px; height: 1200px; overflow: hidden; }
  body {
    background: var(--page-bg);
    display: flex;
    flex-direction: column;
    align-items: center;
    justify-content: center;
    gap: 60px;
  }
  .card {
    position: relative;
    width: 700px;
    height: 400px;
    background: linear-gradient(160deg, var(--card-black) 0%, var(--card-sheen) 45%, var(--card-black) 75%);
    box-shadow: 0 10px 26px rgba(0,0,0,0.28);
    overflow: hidden;
  }
  .badge {
    position: absolute;
    border-radius: 50%;
    background: var(--badge-white);
    border: 9px solid var(--badge-ring);
    display: flex;
    align-items: center;
    justify-content: center;
    text-align: center;
    font-family: "Roboto Condensed", sans-serif;
    font-weight: 400;
    color: var(--ink);
    line-height: 1.15;
  }
  .card-front .badge {
    width: 220px; height: 200px;
    left: 240px; top: 100px;
    font-size: 26px;
    padding: 0 24px;
  }
  .card-back .band {
    position: absolute;
    left: 0; right: 0;
    top: 118px; height: 72px;
    background: var(--band-black);
    border-top: 2px solid var(--rule-grey);
  }
  .card-back .rule {
    position: absolute;
    left: 0; right: 0;
    height: 2px;
    background: var(--rule-grey);
  }
  .card-back .rule-a { top: 262px; }
  .card-back .rule-b { top: 298px; }
  .card-back .badge {
    width: 190px; height: 176px;
    left: 480px; top: 34px;
    font-size: 22px;
    padding: 0 20px;
  }
  .holder-name {
    position: absolute;
    left: 58px; top: 196px;
    font-family: "Roboto Condensed", sans-serif;
    font-size: 30px;
    color: var(--text-white);
  }
  .holder-role {
    position: absolute;
    left: 72px; top: 234px;
    font-family: "Crimson Text", serif;
    font-size: 19px;
    color: var(--text-soft);
  }
  .contact {
    position: absolute;
    font-family: "Crimson Text", serif;
    font-size: 20px;
    color: var(--text-white);
    display: flex;
    align-items: center;
    gap: 8px;
  }
  .contact svg { width: 15px; height: 15px; fill: var(--text-white); }
  .contact-email { right: 40px; top: 218px; }
  .contact-phone { left: 40px; top: 320px; }
  .contact-web { left: 40px; top: 352px; }
</style>
</head>
<body>

  <section class="card card-front" aria-label="Card front">
    <div class="badge">Birchway Canine Training</div>
  </section>

  <section class="card card-back" aria-label="Card back">
    <div class="band"></div>
    <div class="rule rule-a"></div>
    <div class="rule rule-b"></div>
    <div class="badge">Birchway Canine Training</div>

    <p class="holder-name">Lowell Spratt</p>
    <p class="holder-role">Dog owners</p>

    <p class="contact contact-email">
      <svg viewBox="0 0 16 16" aria-hidden="true"><path d="M1 3h14v10H1z M2 4l6 5 6-5" fill="none" stroke="#f2f2f2" stroke-width="1.4"/></svg>
      info@birchwaycanine.example
    </p>
    <p class="contact contact-phone">
      <svg viewBox="0 0 16 16" aria-hidden="true"><path d="M4 1l3 3-1.5 2a9 9 0 0 0 4.5 4.5L12 9l3 3-2 3C7 15 1 9 1 3z"/></svg>
      281-904-3376
    </p>
    <p class="contact contact-web">
      <svg viewBox="0 0 16 16" aria-hidden="true"><circle cx="8" cy="8" r="6.5" fill="none" stroke="#f2f2f2" stroke-width="1.4"/><path d="M1.5 8h13M8 1.5c-3 3.5-3 9.5 0 13M8 1.5c3 3.5 3 9.5 0 13" fill="none" stroke="#f2f2f2" stroke-width="1.2"/></svg>
      www.birchwaycanine.example
    </p>
  </section>

</body>
</html>
```